Stylish business cards for KV7

To create an appealing and professional business card design for a WOMEN Owned Construction Supply Company.
2 sided card. Incorporate brand elements, curvy, colorful, sleek and bright. No solid white background. attached samples of styles added shapes/ribbons. Want something with that WOW that looks awesome, factor. It is a new logo, so feel free to mess with logo colors in the blue and teal factors that can look good with both dark and light background. If you want to try a watermark with just the KV7, without the "Supply" that might look cool to.

Industry/Entity Type

Women owned construction supply company

Contact Information for Business Card

Name, Title, and phone number and email, web page. maybe spot for qr code.

Font styles to use
Sans Serif

Requirements
Nice to have
• would love to see colors, maybe stylish ribbon dividers or some sort of 2 or 3 tone color card that compliments logo.
Should not have
• Please do not have all white background. Do not include Home/reale state/ or building images.

```html
<!DOCTYPE html>
<html lang="en">
<head>
<meta charset="utf-8">
<title>KV7 Supply – Business Cards</title>
<link rel="stylesheet" href="https://fonts.googleapis.com/css2?family=Montserrat:wght@400;500;700&display=swap">
<style>
  :root {
    --navy: #1b3755;
    --teal: #2292b8;
    --paper: #f3f3f3;
    --ink: #1f2a36;
    --backdrop: #1e1e1e;
  }
  * { margin: 0; padding: 0; box-sizing: border-box; }
  html, body { width: 1200px; height: 1059px; overflow: hidden; background: var(--backdrop); }
  body { position: relative; font-family: "Montserrat", sans-serif; }

  .card {
    position: absolute;
    width: 690px;
    height: 392px;
    border-radius: 20px;
    overflow: hidden;
  }
  .card--front { left: 256px; top: 89px; background: var(--paper); }
  .card--back  { left: 254px; top: 547px; background: var(--navy); }

  .card__wave { position: absolute; inset: 0; width: 100%; height: 100%; }

  .brand {
    position: absolute;
    font-weight: 700;
    letter-spacing: 0.5px;
    white-space: nowrap;
    display: flex;
    align-items: center;
    gap: 12px;
  }
  .brand__dot { width: 14px; height: 14px; border-radius: 50%; background: var(--teal); }
  .card--front .brand { left: 34px; top: 118px; font-size: 36px; color: var(--navy); }
  .card--back .brand  { left: 50%; top: 50%; transform: translate(-50%, -50%); font-size: 56px; color: var(--paper); }
  .card--back .brand__dot { width: 20px; height: 20px; }

  .person { position: absolute; right: 33px; top: 50px; text-align: right; }
  .person__name { font-size: 24px; font-weight: 700; color: var(--navy); letter-spacing: 0.3px; line-height: 1; }
  .person__name span { color: var(--teal); }
  .person__title { font-size: 14px; color: var(--ink); margin-top: 4px; }

  .contact {
    position: absolute;
    right: 33px;
    top: 232px;
    text-align: right;
    color: var(--paper);
    font-size: 14.5px;
    line-height: 20px;
  }
  .contact__address { margin-bottom: 10px; }
  .contact__line { display: flex; justify-content: flex-end; align-items: center; gap: 7px; height: 25px; }
  .contact__icon { width: 13px; height: 13px; flex: none; }
</style>
</head>
<body>

<section class="card card--front" aria-label="Card front">
  <svg class="card__wave" viewBox="0 0 690 392" preserveAspectRatio="none" aria-hidden="true">
    <path d="M0,222 C60,262 130,298 230,288 C340,276 460,162 558,158 C612,156 652,176 690,200 L690,392 L0,392 Z" fill="var(--navy)"/>
    <path d="M0,210 C55,250 120,280 225,272 C330,263 440,175 545,153" fill="none" stroke="var(--teal)" stroke-width="7" stroke-linecap="round"/>
    <path d="M130,316 C260,300 420,200 560,153" fill="none" stroke="var(--paper)" stroke-width="2"/>
  </svg>

  <div class="brand"><span class="brand__dot"></span>KV7 Supply</div>

  <div class="person">
    <p class="person__name">DELIA <span>MARSH</span></p>
    <p class="person__title">CEO/Founder</p>
  </div>

  <div class="contact">
    <p class="contact__address">P.O Box 3160 Harbour Road<br>Westfield QN 40217</p>
    <p class="contact__line">418.630.2754
      <svg class="contact__icon" viewBox="0 0 24 24" aria-hidden="true"><path fill="var(--teal)" d="M6.6 10.8a15.1 15.1 0 0 0 6.6 6.6l2.2-2.2a1 1 0 0 1 1-.25 11.4 11.4 0 0 0 3.6.57 1 1 0 0 1 1 1V20a1 1 0 0 1-1 1A17 17 0 0 1 3 4a1 1 0 0 1 1-1h3.5a1 1 0 0 1 1 1c0 1.25.2 2.45.57 3.57a1 1 0 0 1-.25 1z"/></svg>
    </p>
    <p class="contact__line">hello@kv7supply.com.au
      <svg class="contact__icon" viewBox="0 0 24 24" aria-hidden="true"><rect x="2" y="5" width="20" height="14" rx="1" fill="var(--teal)"/><path d="M2 6l10 7 10-7" fill="none" stroke="var(--navy)" stroke-width="1.6"/></svg>
    </p>
    <p class="contact__line">www.kv7supply.com.au
      <svg class="contact__icon" viewBox="0 0 24 24" aria-hidden="true"><g fill="none" stroke="var(--teal)" stroke-width="1.8"><circle cx="12" cy="12" r="9.5"/><ellipse cx="12" cy="12" rx="4" ry="9.5"/><path d="M2.5 12h19M4 7h16M4 17h16"/></g></svg>
    </p>
  </div>
</section>

<section class="card card--back" aria-label="Card back">
  <div class="brand"><span class="brand__dot"></span>KV7 Supply</div>
</section>

</body>
</html>
```